Tarlow Plumbing & Heating Limited needs a service and maintenance contract document design

Tarlow Plumbing & Heating Limited are a well established family owned and operated company.

We currently offer installation, service and repair services for gas, plumbing, heating and electrical work. We wish to offer service and maintenance plans for plumbing, heating and electrical for our domestic clients in the UK. We would like the brochure to incorporate our company logo and colours, and reflect the reliable, quality, 5 star service we offer our clients.
I have attached a brochure that a friends company uses to give a good idea of the structure of the plans we wish to offer. We want to give our customers a choice in what packages best suit their needs. However, the pricing structure and certain elements/content of what we offer will be slightly different due to our geographical location.

We would like to have the basic structure of the brochure put in place and the
text content editable to our specific needs. Looking for advice on this but we do have Acrobat DC if we need to edit the text ourselves?

We use our logo with "TARLOW" in white over a grey backgound.

Our website is - www.tarlow.plumbing
Facebook and twitter handle is - @TarlowHeating

Target Market(s)

UK domestic plumbing, heating, natural gas, LPG and electrical market. Both private homeowners and landlords. Please see both the domestic and landlord document files attached for an idea on what we'd like.

Colors

Designer to choose colors to be used in the design.

Requirements
Must have
• Would like the finished design to incorporate the branding and colours we already use. Professional, Contemporary designs that will stand out above our competition.
• The content of the brochures MUST be very similar in structure to the files I’ve attached to the brief.
• We are having many designs submitted that are just copying our website content. This is not what we are asking for.
• I would like the icons etc to be redesigned so they are ours and not copied.
• Please also see the Landlords brochure attached to the brief. We would like this to be a separate document but to reflect the same design as the homeowner design you submit.
• The content of the documents will need to be re worded for our own use but I'm happy to change this once the design element is in place.
• A4 sized pages as per the example I've attached
• Must be able to attach the document to our website for clients to download.
Nice to have
• A4 sized pages as per the examples I've attached
Should not have
• Please DO NOT copy the content from our website to create our service plan brochures. This is not what we are after. As above, we need the brochures to be like the ones we've provided but made to fit our brand.
• Thank you

```html
<!DOCTYPE html>
<html lang="en">
<head>
<meta charset="utf-8">
<title>Tarlow Plumbing &amp; Heating – Flyer</title>
<link rel="stylesheet" href="https://fonts.googleapis.com/css2?family=Montserrat:wght@500;600;700&display=swap">
<style>
  :root {
    --ink: #111418;
    --slate: #28323d;
    --blue: #0aa0e6;
    --blue-deep: #0068bd;
    --orange: #f7941d;
    --red: #ec2227;
    --white: #ffffff;
    --backdrop: #e9e9e9;
  }
  html, body {
    margin: 0;
    width: 946px;
    height: 1200px;
    overflow: hidden;
    background: var(--backdrop);
  }
  .flyer {
    position: absolute;
    left: 56px;
    top: 10px;
    width: 834px;
    height: 1180px;
    display: block;
    font-family: "Montserrat", sans-serif;
  }
  .brand-name { font-weight: 700; font-size: 72px; fill: var(--white); letter-spacing: -1px; }
  .brand-sub { font-weight: 700; font-size: 17px; fill: var(--white); letter-spacing: 9px; }
  .headline { font-weight: 700; font-size: 38px; fill: var(--ink); }
  .care-intro { font-weight: 600; font-size: 29px; fill: var(--blue); }
  .care-title { font-weight: 600; font-size: 27px; fill: var(--orange); }
  .service { font-weight: 600; font-size: 14px; fill: var(--slate); letter-spacing: .3px; }
  .values { font-weight: 600; font-size: 31px; fill: var(--white); }
  .website { font-weight: 600; font-size: 26px; fill: var(--white); }
  .icon { fill: var(--blue-deep); }
  .icon-warm { fill: var(--red); }
</style>
</head>
<body>
<svg class="flyer" viewBox="0 0 939 1328" xmlns="http://www.w3.org/2000/svg">
  <defs>
    <linearGradient id="bandBlue" x1="0" x2="1" y1="0" y2="0">
      <stop offset="0" stop-color="#0aa8ea"/>
      <stop offset="1" stop-color="#0070c0"/>
    </linearGradient>
    <linearGradient id="warm" x1="0" x2="1" y1="0" y2="0">
      <stop offset="0" stop-color="#ec2227"/>
      <stop offset="1" stop-color="#f7941d"/>
    </linearGradient>
    <linearGradient id="footBlue" x1="0" x2="1" y1="1" y2="0">
      <stop offset="0" stop-color="#18aef0"/>
      <stop offset="1" stop-color="#0068bd"/>
    </linearGradient>
    <linearGradient id="photoTone" x1="0" x2="1" y1="0" y2="1">
      <stop offset="0" stop-color="#eef4fb"/>
      <stop offset=".55" stop-color="#d3e3f4"/>
      <stop offset="1" stop-color="#eaf1f8"/>
    </linearGradient>
  </defs>

  <!-- page -->
  <rect class="page" width="939" height="1328" fill="var(--white)"/>

  <!-- top band -->
  <rect y="0" width="939" height="31" fill="url(#bandBlue)"/>
  <rect y="40" width="939" height="360" fill="var(--slate)"/>

  <!-- kitchen photo area -->
  <path role="img" aria-label="Photo of a bright white fitted kitchen with a wall-mounted boiler"
        d="M430 360 C560 300 760 250 939 270 L939 920 C820 900 640 960 500 990 C380 880 300 640 430 360 Z"
        fill="url(#photoTone)"/>

  <!-- photo frame arcs -->
  <path d="M430 360 C300 600 360 860 500 990 L490 990 C330 850 280 600 420 365 Z" fill="var(--orange)"/>
  <path d="M418 368 C270 600 330 860 492 992 L470 985 C300 850 250 600 400 375 Z" fill="var(--blue)"/>

  <!-- header wave -->
  <path d="M0 40 L939 40 L939 200 C760 215 600 300 440 360 C280 420 120 380 0 300 Z" fill="var(--slate)"/>
  <path d="M0 300 C120 380 280 420 440 360 C300 430 120 430 0 365 Z" fill="var(--blue)"/>
  <path d="M440 360 C600 300 760 215 939 200 L939 245 C780 245 620 300 440 360 Z" fill="url(#warm)"/>
  <path d="M470 352 C620 300 780 255 939 255 L939 268 C780 268 630 310 470 352 Z" fill="var(--white)"/>

  <!-- brand -->
  <circle cx="125" cy="180" r="52" fill="var(--blue)"/>
  <text class="brand-name" x="210" y="196">TARLOW</text>
  <text class="brand-sub" x="213" y="221">PLUMBING &amp; HEATING</text>

  <!-- headline -->
  <text class="headline">
    <tspan x="507" y="405">FRIENDLY,</tspan>
    <tspan x="507" y="455">FAMILY RUN</tspan>
    <tspan x="507" y="505">COMPANY</tspan>
  </text>

  <!-- services -->
  <text class="care-intro" x="54" y="528">We can</text>
  <text class="care-title" x="54" y="559">CARE FOR YOUR</text>

  <g class="service-list">
    <rect class="icon" x="68" y="592" width="24" height="16" rx="2"/>
    <text class="service" x="116" y="606">CENTRAL HEATING</text>

    <rect class="icon" x="71" y="624" width="18" height="24" rx="2"/>
    <text class="service" x="118" y="642">BOILERS</text>

    <path class="icon" d="M68 676 h10 v6 h6 v-14 h5 v19 h-21 Z"/>
    <text class="service" x="118" y="686">GENERAL PLUMBING</text>

    <path class="icon" d="M64 718 h30 l-3 12 h-24 Z"/>
    <text class="service" x="118" y="730">BATHROOMS</text>

    <rect class="icon" x="68" y="759" width="24" height="24" rx="4"/>
    <circle cx="80" cy="771" r="7" fill="none" stroke="var(--white)" stroke-width="2"/>
    <text class="service" x="118" y="774">POWER FLUSHING</text>

    <rect x="68" y="800" width="22" height="24" fill="none" stroke="var(--blue-deep)" stroke-width="3"/>
    <path class="icon-warm" d="M79 806 c5 6 6 10 2 14 h-5 c-3 -4 0 -9 3 -14 Z"/>
    <text class="service" x="118" y="817">UNDERFLOOR HEATING</text>

    <path d="M66 846 h10 v8 h10" fill="none" stroke="var(--orange)" stroke-width="3"/>
    <text class="service" x="118" y="860">LPG</text>

    <rect class="icon" x="70" y="884" width="8" height="24" rx="2"/>
    <rect class="icon" x="82" y="882" width="9" height="12" rx="2"/>
    <text class="service" x="118" y="904">BOILER INSTALLATION</text>
  </g>

  <!-- footer waves -->
  <path d="M0 978 C140 1040 300 1040 500 990 C660 950 800 880 939 915 L939 1328 L0 1328 Z" fill="var(--slate)"/>
  <path d="M0 1020 C200 1070 420 1060 600 1010 C740 970 850 940 939 950 L939 1328 L0 1328 Z" fill="url(#warm)"/>
  <path d="M0 1085 C200 1095 420 1060 600 1015 C740 980 850 950 939 960 L939 1328 L0 1328 Z" fill="url(#footBlue)"/>

  <text class="values" x="470" y="1181" text-anchor="middle">LOCAL - PROFESSIONAL- RELIABLE - TRUSTED</text>
  <text class="website" x="470" y="1235" text-anchor="middle">WWW.TARLOW.PLUMBING</text>
</svg>
</body>
</html>
```